KLV Plant Services

We are a heavy diesel mechanical business with additional air con certificates, remapping engine rebuilt

Contact Information for Business Card

Company Name, Director Name, Managing Director, Contact details, email and website

Font styles to use
Serif
Script

```html
<!DOCTYPE html>
<html lang="en">
<head>
<meta charset="utf-8">
<title>KLV Plant Services – Business Card</title>
<link href="https://fonts.googleapis.com/css2?family=Noto+Serif:wght@400;700&display=swap" rel="stylesheet">
<style>
  :root {
    --backdrop: #d6d6d6;
    --card: #f1f1f1;
    --navy: #1b1a63;
    --ink: #1a1a1a;
    --edge: #1b1a63;
  }
  * { box-sizing: border-box; margin: 0; padding: 0; }
  html, body {
    width: 1200px; height: 1051px; overflow: hidden;
    background: var(--backdrop);
    font-family: "Noto Serif", serif;
  }
  .canvas {
    position: relative; width: 1200px; height: 1051px;
  }
  .card {
    position: absolute;
    width: 520px; height: 300px;
    background: var(--card);
    border-bottom: 4px solid var(--edge);
    border-right: 4px solid var(--edge);
    box-shadow: 0 24px 40px rgba(0,0,0,0.18);
  }
  .card--front { left: 50px; top: 376px; }
  .card--back { left: 630px; top: 376px; }

  .brand {
    display: flex; align-items: center; gap: 10px;
    color: var(--navy); font-weight: 700; line-height: 1.1;
  }
  .brand__dot {
    flex: none; border-radius: 50%; background: var(--navy);
  }
  .card--front .brand {
    position: absolute; left: 30px; top: 100px; width: 200px;
    font-size: 28px;
  }
  .card--front .brand__dot { width: 18px; height: 18px; }

  .divider {
    position: absolute; left: 250px; top: 50px;
    width: 2px; height: 200px; background: var(--navy);
  }

  .contact {
    position: absolute; left: 272px; top: 56px; width: 240px;
    color: var(--ink);
  }
  .contact__name {
    color: var(--navy); font-weight: 700; font-size: 21px;
    text-transform: uppercase; letter-spacing: 0.5px;
  }
  .contact__role {
    color: var(--navy); font-size: 15px; margin-bottom: 14px;
  }
  .contact__list { list-style: none; font-size: 15px; line-height: 1.55; }
  .contact__list li { display: flex; align-items: center; gap: 8px; }
  .contact__list svg { width: 13px; height: 13px; flex: none; fill: var(--navy); }
  .contact__address { font-size: 15px; line-height: 1.4; margin-top: 8px; }

  .card--back .brand {
    position: absolute; left: 0; right: 0; top: 0; bottom: 0;
    justify-content: center; font-size: 42px;
  }
  .card--back .brand__dot { width: 26px; height: 26px; }
</style>
</head>
<body>
<main class="canvas">
  <section class="card card--front" aria-label="Business card front">
    <div class="brand"><span class="brand__dot"></span><span>KLV Plant Services</span></div>
    <div class="divider"></div>
    <div class="contact">
      <p class="contact__name">Daniel Hart</p>
      <p class="contact__role">Managing Director</p>
      <ul class="contact__list">
        <li><svg viewBox="0 0 24 24" aria-hidden="true"><path d="M6.6 10.8a15 15 0 0 0 6.6 6.6l2.2-2.2a1 1 0 0 1 1-.25 11.4 11.4 0 0 0 3.6.57 1 1 0 0 1 1 1V20a1 1 0 0 1-1 1A17 17 0 0 1 3 4a1 1 0 0 1 1-1h3.5a1 1 0 0 1 1 1c0 1.25.2 2.45.57 3.57a1 1 0 0 1-.25 1z"/></svg>123 456 789</li>
        <li><svg viewBox="0 0 24 24" aria-hidden="true"><path d="M2 5h20v14H2zm2 2v.5l8 5 8-5V7l-8 5z"/></svg>info@klvplant.com</li>
        <li><svg viewBox="0 0 24 24" aria-hidden="true"><circle cx="12" cy="12" r="10"/></svg>www.klvplant.com</li>
      </ul>
      <p class="contact__address">Your address, City<br>State, Zip 1234</p>
    </div>
  </section>

  <section class="card card--back" aria-label="Business card back">
    <div class="brand"><span class="brand__dot"></span><span>KLV Plant Services</span></div>
  </section>
</main>
</body>
</html>
```